Web Design Project for Audio-Visual & Video Communications Business

We are currently busy with our new Wordpress website and require cutting-edge designs for our Home page. The intro images on the Home Page must give our visitors a quick overview of the services that we sell. These are broken down into 3 different services:

1. Audio-Visual (These include projectors, audio systems, projector screens, specialised brackets, Veltrane control systems, etc)

2. Video Communications products (We sell Marivox and TrueBand equipment)

3. Online Shop (We need the best design to attract our existing and new visitors. The current design on the website was only done to show you what we have on offer)

We prefer to use the current theme but would like you to start building on top of this. This will be an ongoing project during 2013 to ensure that we keep the site fresh and updated.

Target Market(s)

We market our business to the Corporate, Education and Hospitality markets. We do however have individuals that will buy equipment online.

Industry/Entity Type

Building

Requirements
Must have
• The design must consist of 3 independent pages. We have several sliders that we can use on the Home page so you can decide if images and text must be visible at different times.
Nice to have
• You can visit the current draft website for the current look and feel. If you have completely new ideas we might consider them. Visit the site at www.linkwavegroup.co.za.

```html
<!DOCTYPE html>
<html lang="en">
<head>
<meta charset="utf-8">
<title>Linkwave – Leaders in Audio-Visual &amp; Video Communications</title>
<link href="https://fonts.googleapis.com/css2?family=Ubuntu:wght@400;500;700&family=Noto+Sans:wght@400;700&display=swap" rel="stylesheet">
<style>
:root{
  --green:#9ab43c;
  --green-dark:#7f9a2a;
  --charcoal:#3b3b3d;
  --charcoal-deep:#2b2b2d;
  --slate:#4a4a4d;
  --text:#555;
  --line:#dcdcdc;
  --paper:#fff;
}
*{box-sizing:border-box;margin:0;padding:0}
html,body{width:873px;height:1200px;overflow:hidden;background:var(--paper)}
body{position:relative;font-family:"Noto Sans",Arial,sans-serif;color:var(--text);font-size:9px}
a{color:inherit;text-decoration:none}
h2,h3,h4,h5{font-weight:400}
.abs{position:absolute}

/* header */
.top-line{left:0;top:0;width:873px;height:4px;background:var(--green)}
.header{left:0;top:4px;width:873px;height:114px;background:linear-gradient(#fff,#f3f3f3);border-bottom:1px solid #e2e2e2}
.utility{left:408px;top:0;width:247px;height:30px;background:var(--green);clip-path:polygon(0 0,100% 0,96% 100%,4% 100%);color:#fff;font-size:8px;display:flex;align-items:center;justify-content:center;gap:7px}
.utility .sep{opacity:.7}
.search{left:662px;top:10px;width:116px;height:18px;border:1px solid #ccc;border-radius:3px;background:#fff}
.brand{left:100px;top:20px;display:flex;align-items:flex-end;gap:8px}
.brand-dot{width:46px;height:46px;border-radius:50%;background:var(--green)}
.brand-name{font-family:"Ubuntu",sans-serif;font-weight:700;font-size:22px;color:var(--slate)}
.nav{left:454px;top:86px;display:flex;align-items:center;font-family:"Ubuntu",sans-serif;font-size:10px;color:#444}
.nav .home{background:var(--green);color:#fff;padding:5px 12px;border-radius:3px}
.nav span{padding:0 10px}
.nav .sep{padding:0;color:#888}

/* slider */
.band{left:0;top:126px;width:873px;height:310px;background:linear-gradient(90deg,#2f2f31,#4d4d50 50%,#2f2f31)}
.slide{left:94px;top:132px;width:685px;height:298px;background:#fff;padding:4px;overflow:hidden}
.slide-inner{position:relative;width:100%;height:100%;overflow:hidden;background:#f7f8f6}
.scene-meeting{position:absolute;left:0;top:0;width:480px;height:100%;background:linear-gradient(180deg,#e9ecef 0%,#cdd3da 38%,#8d949c 62%,#eef0f1 78%,#c9cdd1 100%)}
.scene-products{position:absolute;left:440px;top:0;width:237px;height:100%;background:linear-gradient(160deg,#f4f5f3 0%,#d4d7da 35%,#8e9298 60%,#e9eaeb 100%)}
.scene-curve{position:absolute;left:0;top:0}
.caption{left:98px;top:358px;width:677px;height:48px;background:rgba(40,40,40,.72);color:#fff;font-family:"Ubuntu",sans-serif;font-size:24px;font-weight:500;padding:9px 0 0 22px}
.arrow{top:264px}

/* feature boxes */
.feature{top:453px;width:219px;height:128px;background:var(--green);border-radius:3px}
.tab{position:absolute;left:14px;top:0;width:191px;height:28px;background:var(--slate);clip-path:polygon(0 0,100% 0,93% 100%,7% 100%);color:#fff;font-family:"Ubuntu",sans-serif;font-size:14px;text-align:center;line-height:28px}
.feature p{position:absolute;left:17px;top:33px;width:192px;color:#fff;font-size:8.2px;line-height:16.8px}
.feature .more{position:absolute;left:17px;top:108px;font-size:8.5px;font-weight:700;color:#2d2d2d}
.product{position:absolute;left:22px;top:46px;width:110px;height:48px;border-radius:50%;background:radial-gradient(#8a8d91,#3a3b3e)}
.product-label{position:absolute;left:146px;top:74px;color:#2d2d2d;font-size:9px;line-height:12px;font-weight:700}
.pager{position:absolute;top:119px;width:16px;height:16px;border-radius:50%;background:var(--slate)}

/* services */
.rule{left:94px;top:606px;width:685px;height:1px;background:var(--line)}
.section-title{font-family:"Ubuntu",sans-serif;font-size:16.5px;font-weight:400;color:#555;top:620px}
.card{width:219px;height:124px;border:1px solid #e0e0e0;border-radius:3px;background:linear-gradient(#fff,#f6f6f6)}
.card h3{position:absolute;left:43px;top:10px;font-family:"Ubuntu",sans-serif;font-weight:500;font-size:13.5px;color:var(--green-dark)}
.card .icon{position:absolute;left:10px;top:7px}
.card p{position:absolute;left:11px;top:42px;width:188px;font-size:8.3px;line-height:14.5px;color:#666}
.card .more{position:absolute;left:11px;top:105px;font-size:8.2px;color:#333}

/* blog */
.post{left:560px;width:219px}
.thumb{position:absolute;left:0;top:0;width:59px;height:52px;border:1px solid #ddd;padding:2px;background:#fff}
.thumb div{width:100%;height:100%;background:linear-gradient(#6b7c8a,#c9d0a8)}
.post h4{position:absolute;left:69px;top:0;width:150px;font-size:9.3px;line-height:13px;font-weight:700;color:var(--green-dark)}
.post p{position:absolute;left:69px;width:150px;font-size:8.5px;line-height:13px;color:#555}
.post .date{position:absolute;left:69px;font-size:7.8px;font-style:italic;color:var(--green-dark)}
.post-rule{left:560px;top:759px;width:219px;height:1px;background:var(--line)}

/* footer */
.footer{left:0;top:935px;width:873px;height:230px;background:var(--charcoal)}
.footer-bar{left:0;top:1165px;width:873px;height:35px;background:var(--charcoal-deep);color:#aaa;font-size:7.6px;text-align:center;line-height:35px}
.footer h5{position:absolute;font-family:"Ubuntu",sans-serif;font-weight:500;font-size:13px;color:#fff;line-height:17px}
.footer p{position:absolute;color:#ccc;font-size:8.4px;line-height:16.8px}
.footer .hl{color:var(--green)}
.email-field{position:absolute;left:618px;top:91px;width:160px;height:20px;border-radius:4px;background:#8a8a8c}
.signup{position:absolute;left:735px;top:124px;width:43px;height:21px;background:var(--green);color:#fff;border-radius:3px;font-size:9px;text-align:center;line-height:21px}
.social{position:absolute;top:184px;width:22px;height:22px;border-radius:3px;background:#5e5e61}
</style>
</head>
<body>

<div class="abs header"></div>
<div class="abs top-line"></div>
<div class="abs utility"><span>Shop</span><span class="sep">|</span><span>My Account</span><span class="sep">|</span><span>Checkout</span><span class="sep">|</span>
  <svg width="12" height="10" viewBox="0 0 12 10"><path d="M1 3h10l-1.5 6h-7z" fill="#3b3b3d"/></svg><span>0 items - R0</span></div>
<div class="abs search">
  <svg class="abs" style="left:97px;top:2px" width="13" height="13" viewBox="0 0 13 13"><circle cx="5" cy="5" r="3.8" fill="none" stroke="#333" stroke-width="1.6"/><path d="M8 8l4 4" stroke="#333" stroke-width="2"/></svg>
</div>

<div class="abs brand"><div class="brand-dot"></div><div class="brand-name">Linkwave</div></div>

<nav class="abs nav">
  <a class="home">HOME</a><span>SHOP</span><span class="sep">|</span><span>ABOUT US</span><span class="sep">|</span><span>BLOG</span><span class="sep">|</span><span>CONTACT US</span>
</nav>

<div class="abs band"></div>
<div class="abs slide">
  <div class="slide-inner">
    <div class="scene-meeting" role="img" aria-label="Business team seated at a meeting table in front of a projector screen"></div>
    <div class="scene-products" role="img" aria-label="Video conferencing displays, cameras, codecs and a speakerphone"></div>
    <svg class="scene-curve" width="677" height="290" viewBox="0 0 677 290">
      <path d="M575 0C500 40 470 120 480 200C486 245 500 275 515 290L677 290L677 0Z" fill="#f6f7f4" opacity=".55"/>
      <path d="M575 0C500 40 470 120 480 200C486 245 500 275 515 290" fill="none" stroke="#9ab43c" stroke-width="7"/>
    </svg>
  </div>
</div>
<div class="abs caption">Leaders in Audio-Visual &amp; Video Communications.</div>
<svg class="abs arrow" style="left:66px" width="20" height="32" viewBox="0 0 20 32"><path d="M16 3L4 16l12 13" fill="none" stroke="#fff" stroke-width="5"/></svg>
<svg class="abs arrow" style="left:786px" width="20" height="32" viewBox="0 0 20 32"><path d="M4 3l12 13L4 29" fill="none" stroke="#fff" stroke-width="5"/></svg>

<section class="abs feature" style="left:94px">
  <div class="tab">Audio Visual</div>
  <p>Exercitationem ullam corporis suscipit labo-riosam, nisi ut aliquid ex ea commodi conse-quatur voluptatem quia voluptas sit asper-natur aut odit aut fugit consequuntur...</p>
  <a class="more">READ MORE</a>
</section>
<section class="abs feature" style="left:327px">
  <div class="tab">Video Communications</div>
  <p>Exercitationem ullam corporis suscipit labo-riosam, nisi ut aliquid ex ea commodi conse-quatur voluptatem quia voluptas sit asper-natur aut odit aut fugit consequuntur...</p>
  <a class="more">READ MORE</a>
</section>
<section class="abs feature" style="left:560px">
  <div class="tab">Online Shopping</div>
  <div class="product" role="img" aria-label="Conference speakerphone product"></div>
  <div class="product-label">Audio<br>Conferencing</div>
  <div class="pager" style="left:88px"></div>
  <div class="pager" style="left:114px"></div>
  <svg class="abs" style="left:93px;top:124px" width="6" height="6" viewBox="0 0 6 6"><path d="M5 0v6L0 3z" fill="#fff"/></svg>
  <svg class="abs" style="left:120px;top:124px" width="6" height="6" viewBox="0 0 6 6"><path d="M0 0v6l5-3z" fill="#fff"/></svg>
</section>

<div class="abs rule"></div>
<h2 class="abs section-title" style="left:94px">Services that we offer</h2>
<h2 class="abs section-title" style="left:560px">Recent Blog Posts</h2>

<svg width="0" height="0" style="position:absolute">
  <symbol id="icon-cycle" viewBox="0 0 26 26"><circle cx="13" cy="13" r="13" fill="#3b3b3d"/><path d="M7 12a6 6 0 0 1 11-3M19 14a6 6 0 0 1-11 3" fill="none" stroke="#fff" stroke-width="2"/><path d="M19 6v4h-4zM7 20v-4h4z" fill="#fff"/></symbol>
  <symbol id="icon-grid" viewBox="0 0 26 26"><circle cx="13" cy="13" r="13" fill="#3b3b3d"/><rect x="7" y="7" width="12" height="12" fill="none" stroke="#fff" stroke-width="1.8"/><path d="M7 11h12M7 15h12M11 7v12M15 7v12" stroke="#fff" stroke-width="1.4"/></symbol>
</svg>

<article class="abs card" style="left:94px;top:652px">
  <svg class="icon" width="26" height="26"><use href="#icon-cycle"/></svg>
  <h3>Consultation &amp; Design</h3>
  <p>Linkwave offers a complete range of consultation &amp; design services. Let us assist you with designing your next Audio-Visual &amp; Video Communications system.</p>
  <a class="more">READ MORE</a>
</article>
<article class="abs card" style="left:327px;top:652px">
  <svg class="icon" width="26" height="26"><use href="#icon-grid"/></svg>
  <h3>Project Management</h3>
  <p>Linkwave offers complete project man-agement services for our Audio-Visual &amp; Video Communications installations. We also offer this service as a standalone option.</p>
  <a class="more">READ MORE</a>
</article>
<article class="abs card" style="left:94px;top:788px">
  <svg class="icon" width="26" height="26"><use href="#icon-grid"/></svg>
  <h3>Supply &amp; Installation</h3>
  <p>Linkwave have access to all the major professional brands in South Africa and can supply and install these products for you. All our installations are 100% guaranteed!</p>
  <a class="more">READ MORE</a>
</article>
<article class="abs card" style="left:327px;top:788px">
  <svg class="icon" width="26" height="26"><use href="#icon-cycle"/></svg>
  <h3>Onsite Support Personal</h3>
  <p>Linkwave provide industry trained per-sonal that we host at your own offices. No need to worry about training IT personal to maintain your AV &amp; Video Communications services.</p>
  <a class="more">READ MORE</a>
</article>

<article class="abs post" style="top:651px">
  <div class="thumb"><div role="img" aria-label="Video conferencing suite on screens"></div></div>
  <h4>Marivox ClearStage CloudLink Suite</h4>
  <p style="top:27px">Marivox recently announced the release of their new ground break-ing products for the video collaboration...</p>
  <span class="date" style="top:82px">Posted on March 16th, 2013</span>
</article>
<div class="abs post-rule"></div>
<article class="abs post" style="top:780px">
  <div class="thumb"><div role="img" aria-label="Video conferencing system with display"></div></div>
  <h4>TrueBand Fusion Series</h4>
  <p style="top:13px">The TrueBand Fusion Series combines best-in-class HD video, audio and presentation capabilities in a bril-liantly...</p>
  <span class="date" style="top:68px">Posted on March 16th, 2013</span>
</article>
<a class="abs" style="left:562px;top:900px;font-size:9.3px;color:#333">READ ALL BLOG POSTS</a>

<footer class="abs footer">
  <h5 style="left:96px;top:30px">About Us</h5>
  <p style="left:95px;top:57px;width:160px">Linkwave is the leading Audio-Visual &amp; Video Communications firm in South Africa.</p>
  <p style="left:95px;top:124px;width:160px">Our team comes with more than 16 years experience in the Corporate, Education and Hospitality markets.</p>
  <p class="hl" style="left:95px;top:191px">Read More &gt;</p>

  <h5 style="left:274px;top:30px">Recent Tweets</h5>
  <p style="left:273px;top:57px;width:150px">Just posted: "Linkwave – Marivox ClearStage CloudLink Suite"( <span class="hl">http://t.co/xK4mR7pLd2</span> ) on Tue Mar 19 2013 23:28:50 GMT+0530 (India Standard Time)</p>

  <h5 style="left:443px;top:30px">Contact Us</h5>
  <p style="left:443px;top:57px;width:160px">The Forum, Harbour Park,<br>Cape Town, South Africa,<br>7450<br>Phone: <span class="hl">+27 21 555-0142</span><br>Email: <span class="hl">info@linkwavegroup.co.za</span></p>

  <h5 style="left:618px;top:30px">Sign Up for Our<br>Newsletter</h5>
  <p style="left:618px;top:75px;color:#fff">Email Address</p>
  <div class="email-field"></div>
  <div class="signup">Sign Up</div>
  <h5 style="left:618px;top:158px">Connect Us</h5>
  <div class="social" style="left:619px" aria-label="Social profile"></div>
  <div class="social" style="left:648px" aria-label="Social profile"></div>
  <div class="social" style="left:677px" aria-label="News feed"></div>
  <div class="social" style="left:706px" aria-label="Video channel"></div>
</footer>
<div class="abs footer-bar">Copyright 2013 Linkwave Group (Pty) Ltd. | All Rights Reserved | Leaders in Audio-Visual &amp; Video Communications.</div>

</body>
</html>
```